Ward Compass Business Card Design*

We need a business card design for our company Ward Compass. Our company is specialized in providing online consulting services regarding medical institutions, hospitals and doctors. We work with patients worldwide looking to choose between healthcare providers. We have a website you may use as a reference, where we list doctors and clinics worldwide. So we target Medical providers as well as patients worldwide.
Target Market(s)
Medical Providers and patients around the world
Industry/Entity Type
Medical
Contact Information for Business Card
Salwa Kettani
CEO
+90 612 348 2175
info@wardcompass.example
www.wardcompass.example
14 Annakhil 7 H.R.B. Rabat, Morocco
Requirements
Must have
- Company logo/name on one full side, personal info and smaller logo and company name on the other side.
Nice to have
- Smart and elegant design

```html
<!DOCTYPE html>
<html lang="en">
<head>
<meta charset="utf-8">
<title>Ward Compass – Business Card</title>
<link rel="stylesheet" href="https://fonts.googleapis.com/css2?family=Montserrat:wght@400;600;700&family=Roboto:wght@400;500&display=swap">
<style>
  :root {
    --backdrop: #e9e6e1;
    --card-white: #f4f4f4;
    --brand-blue: #1f4d96;
    --brand-blue-deep: #173d7c;
    --pattern-blue: #2c58a3;
    --band-grey: #a9abae;
    --ink-white: #ffffff;
    --shadow: rgba(0, 0, 0, 0.22);
  }
  * { box-sizing: border-box; margin: 0; padding: 0; }
  html, body { width: 1200px; height: 780px; overflow: hidden; }
  body {
    background: var(--backdrop);
    position: relative;
    font-family: "Roboto", Arial, sans-serif;
  }
  .card {
    position: absolute;
    top: 235px;
    width: 540px;
    height: 310px;
    border-radius: 4px;
    overflow: hidden;
    box-shadow: 0 10px 24px var(--shadow);
  }
  .card--front { left: 40px; background: var(--card-white); }
  .card--back { left: 620px; background: var(--brand-blue); }

  .front-shapes { position: absolute; inset: 0; }

  .wordmark {
    position: absolute;
    display: flex;
    align-items: center;
    gap: 12px;
  }
  .wordmark__dot {
    width: 30px; height: 30px;
    border-radius: 50%;
    background: var(--brand-blue);
  }
  .wordmark__name {
    font-family: "Montserrat", Arial, sans-serif;
    font-weight: 600;
    letter-spacing: 1.5px;
    text-transform: uppercase;
  }
  .card--front .wordmark { left: 34px; top: 186px; }
  .card--front .wordmark__name { color: var(--brand-blue); font-size: 22px; }

  .contact {
    position: absolute;
    right: 26px;
    top: 46px;
    text-align: right;
    color: var(--ink-white);
  }
  .contact__name {
    font-family: "Montserrat", Arial, sans-serif;
    font-size: 16px;
    font-weight: 700;
    letter-spacing: 0.3px;
    text-transform: uppercase;
  }
  .contact__role {
    font-family: "Montserrat", Arial, sans-serif;
    font-size: 12px;
    font-weight: 400;
    margin-top: 2px;
  }
  .contact__list { list-style: none; margin-top: 34px; }
  .contact__item {
    display: flex;
    justify-content: flex-end;
    align-items: center;
    gap: 8px;
    font-size: 12px;
    line-height: 1;
    margin-bottom: 9px;
  }
  .contact__icon {
    width: 15px; height: 15px;
    border-radius: 50%;
    background: var(--ink-white);
    display: flex; align-items: center; justify-content: center;
  }
  .contact__icon svg { width: 9px; height: 9px; }

  .back-field {
    position: absolute;
    inset: 0;
    background: radial-gradient(ellipse at 40% 35%, var(--pattern-blue), var(--brand-blue) 60%, var(--brand-blue-deep));
  }
  .card--back .wordmark { right: 28px; bottom: 26px; }
  .card--back .wordmark__dot { background: var(--ink-white); width: 24px; height: 24px; }
  .card--back .wordmark__name { color: var(--ink-white); font-size: 15px; }
</style>
</head>
<body>

  <section class="card card--front" aria-label="Business card front">
    <svg class="front-shapes" viewBox="0 0 540 310" width="540" height="310" aria-hidden="true">
      <path d="M300 0 C332 120 304 232 232 310 L540 310 L540 0 Z" fill="var(--band-grey)"/>
      <path d="M320 0 C352 120 332 232 262 310 L540 310 L540 0 Z" fill="var(--brand-blue)"/>
    </svg>

    <div class="wordmark">
      <span class="wordmark__dot"></span>
      <span class="wordmark__name">Ward Compass</span>
    </div>

    <div class="contact">
      <p class="contact__name">Salwa Kettani</p>
      <p class="contact__role">CEO</p>
      <ul class="contact__list">
        <li class="contact__item">+90 612 348 2175
          <span class="contact__icon"><svg viewBox="0 0 10 10"><path d="M2 1 L4 1 L4.6 3 L3.5 3.8 C4 5 5 6 6.2 6.5 L7 5.4 L9 6 L9 8 C9 8.6 8.6 9 8 9 C4.5 9 1 5.5 1 2 C1 1.4 1.4 1 2 1 Z" fill="var(--brand-blue)"/></svg></span>
        </li>
        <li class="contact__item">info@wardcompass.example
          <span class="contact__icon"><svg viewBox="0 0 10 10"><rect x="1" y="2.5" width="8" height="5" fill="none" stroke="var(--brand-blue)" stroke-width="1"/><path d="M1 2.5 L5 5.5 L9 2.5" fill="none" stroke="var(--brand-blue)" stroke-width="1"/></svg></span>
        </li>
        <li class="contact__item">www.wardcompass.example
          <span class="contact__icon"><svg viewBox="0 0 10 10"><circle cx="5" cy="5" r="3.8" fill="none" stroke="var(--brand-blue)" stroke-width="0.9"/><ellipse cx="5" cy="5" rx="1.6" ry="3.8" fill="none" stroke="var(--brand-blue)" stroke-width="0.8"/><path d="M1.2 5 H8.8" stroke="var(--brand-blue)" stroke-width="0.8"/></svg></span>
        </li>
      </ul>
    </div>
  </section>

  <section class="card card--back" aria-label="Business card back">
    <div class="back-field" role="img" aria-label="Faint repeating brand pattern in lighter blue tones"></div>
    <div class="wordmark">
      <span class="wordmark__dot"></span>
      <span class="wordmark__name">Ward Compass</span>
    </div>
  </section>

</body>
</html>
```